Vantiqo custom business card design

Need a authentic, innovative business card design for a new mobile app business. I am uploading a few screen images from our app for you to view. I would like app design theme to match business card design. I can also send logo images.

```html
<!DOCTYPE html>
<html lang="en">
<head>
<meta charset="utf-8">
<title>Vantiqo Business Card</title>
<link href="https://fonts.googleapis.com/css2?family=Montserrat:wght@800&family=Open+Sans:wght@400;600;700&display=swap" rel="stylesheet">
<style>
  :root {
    --backdrop: #5e5e5e;
    --card-light: #ededed;
    --brand-purple: #620090;
    --ink-dark: #1f1f1f;
    --ink-light: #ffffff;
    --rule: rgba(255, 255, 255, 0.55);
  }
  * { margin: 0; padding: 0; box-sizing: border-box; }
  html, body {
    width: 1200px;
    height: 900px;
    overflow: hidden;
    background: var(--backdrop);
  }
  .canvas {
    position: relative;
    width: 1200px;
    height: 900px;
  }
  .card {
    position: absolute;
    top: 235px;
    width: 414px;
    height: 414px;
    border-radius: 50%;
  }
  .card-front {
    left: 184px;
    background: var(--card-light);
  }
  .card-back {
    left: 623px;
    background: var(--brand-purple);
    color: var(--ink-light);
    font-family: "Open Sans", Arial, sans-serif;
    text-align: center;
  }
  .brand-dot {
    position: absolute;
    left: 157px;
    top: 90px;
    width: 100px;
    height: 100px;
    border-radius: 50%;
    background: var(--brand-purple);
  }
  .brand-name {
    position: absolute;
    left: 0;
    right: 0;
    top: 272px;
    text-align: center;
    font-family: "Montserrat", Arial, sans-serif;
    font-weight: 800;
    font-size: 46px;
    color: var(--ink-dark);
    line-height: 1;
  }
  .contact-block {
    position: absolute;
    left: 0;
    right: 0;
    top: 84px;
  }
  .person-name {
    font-family: "Montserrat", Arial, sans-serif;
    font-weight: 800;
    font-size: 26px;
    line-height: 32px;
    letter-spacing: 0.3px;
  }
  .person-role {
    font-size: 19px;
    line-height: 24px;
  }
  .divider {
    width: 206px;
    height: 1px;
    margin: 10px auto 11px;
    background: var(--rule);
  }
  .contact-line {
    font-size: 19px;
    line-height: 24.5px;
  }
  .contact-line .label { font-weight: 700; }
  .web { font-weight: 700; }
  .address { font-size: 19px; line-height: 24px; }
</style>
</head>
<body>
  <main class="canvas">
    <section class="card card-front" aria-label="Card front">
      <div class="brand-dot"></div>
      <div class="brand-name">Vantiqo</div>
    </section>

    <section class="card card-back" aria-label="Card back">
      <div class="contact-block">
        <div class="person-name">MARCUS ELLERY</div>
        <div class="person-role">Managing Director</div>
        <div class="divider"></div>
        <div class="contact-line"><span class="label">P:</span> 055-210 384 617</div>
        <div class="contact-line"><span class="label">M:</span> 055-210 384 617</div>
        <div class="contact-line"><span class="label">E:</span> hello@vantiqo.app</div>
        <div class="contact-line web">www.vantiqo.app</div>
        <div class="divider"></div>
        <div class="address">48 Harbour Lane, Suite 9</div>
        <div class="address">Eastvale, 204518.</div>
      </div>
    </section>
  </main>
</body>
</html>
```